Brightway Haus Inc. Business Card Design

Brightway Haus Inc. is in search of a great clean design for our business cards!

Looking to incorporate our full logo and watermark on side one (however, I am open to having the text and watermark separated within the design.)

On side two, I am looking to have contact information (Name, Position, Phone #, Email, Website (www.thebrightwayhaus.ca). Can have the logo and/or watermark as part of the design if applicable.

Please add tagline "Where Shine Counts" on either side 1 or 2. This tagline can be in a sans serif, serif or cursive font as long as it compliments overall design. Capitalization can be title or sentence case depending on how it fits within the design.

Get creative!! Looking for a clean, crisp, premium design! Looking for a glossy card finish with spot UV features when printed. Cards will also be printed with rounded corners. Standard dimensions (3.5 x 2).

Target Market(s)

B2B - primary clients are business owners or property management corporations. (residential jobs are few and far between)

Industry/Entity Type

Business

Contact Information for Business Card

- clean, crisp design
- double sided
- spot UV accents and glossy finish upon printing
- standard business card size (3.5 x 2) with rounded corners
- please see project description for requirements per side

Font styles to use
Sans Serif

Requirements
Must have
• - adequate bleeds with print ready files
• - cohesive design elements between side 1 & 2
• - spot UV elements (can be on both sides or just one, use your discretion)
• - colour pallet should match the logo file provided
• - incorporate tagline "where shine counts" (this tagline can be in a serif or sans serif font as long as it is complimentary to the overall design.
Nice to have
• - Premium elements with a clean design
Should not have
• - Please omit cartoon or whimsical like designs, think premium.
• - Colours should not stray from the pallet of the provided logo.

```html
<!DOCTYPE html>
<html lang="en">
<head>
<meta charset="utf-8">
<title>Brightway Haus Inc. Business Card</title>
<link rel="stylesheet" href="https://fonts.googleapis.com/css2?family=Open+Sans:wght@400;600;700&display=swap">
<style>
  :root {
    --teal: #10b7ba;
    --navy: #1b2453;
    --white: #ffffff;
    --stage: #2b2b2b;
    --rule: rgba(255,255,255,0.75);
  }
  * { margin: 0; padding: 0; box-sizing: border-box; }
  html, body { width: 1200px; height: 960px; overflow: hidden; }
  body {
    background: var(--stage);
    font-family: "Open Sans", Arial, sans-serif;
    position: relative;
  }
  .card {
    position: absolute;
    width: 600px;
    border-radius: 22px;
    overflow: hidden;
  }
  .card-front { left: 314px; top: 113px; height: 343px; background: var(--white); }
  .card-back { left: 311px; top: 473px; height: 341px; background: var(--navy); }

  .front-shape { position: absolute; inset: 0; }

  .contact {
    position: absolute;
    left: 32px;
    top: 68px;
    color: var(--white);
    font-size: 14.5px;
    line-height: 19px;
  }
  .contact-name { color: var(--navy); font-weight: 700; font-size: 15px; line-height: 18px; }
  .contact-role { font-size: 15px; line-height: 18px; margin-bottom: 26px; }
  .contact-address { margin-bottom: 3px; }
  .contact-list { list-style: none; }
  .contact-list li { display: flex; align-items: center; gap: 9px; }
  .contact-list svg { width: 12px; height: 12px; flex: none; fill: var(--navy); }

  .brand {
    position: absolute;
    display: flex;
    align-items: center;
    font-weight: 700;
    white-space: nowrap;
    letter-spacing: -0.5px;
  }
  .brand-mark { display: block; flex: none; }
  .brand-front { left: 300px; top: 156px; color: var(--navy); font-size: 23px; gap: 8px; }
  .brand-front .brand-mark { width: 26px; height: 26px; background: var(--teal); }
  .brand-back { left: 0; right: 0; top: 124px; justify-content: center; color: var(--white); font-size: 40px; gap: 12px; }
  .brand-back .brand-mark { width: 40px; height: 40px; background: var(--white); }

  .tagline {
    position: absolute;
    left: 100px;
    right: 100px;
    top: 275px;
    display: flex;
    align-items: center;
    gap: 2px;
    color: var(--white);
    font-weight: 600;
    font-size: 17px;
    white-space: nowrap;
  }
  .tagline::before, .tagline::after { content: ""; flex: 1; height: 1px; }
  .tagline::before { background: linear-gradient(to right, transparent, var(--rule)); }
  .tagline::after { background: linear-gradient(to left, transparent, var(--rule)); }
</style>
</head>
<body>
  <section class="card card-front">
    <svg class="front-shape" viewBox="0 0 600 343" aria-hidden="true">
      <path d="M291 0 C238 70 236 262 438 343 L0 343 L0 0 Z" fill="var(--navy)"/>
      <path d="M291 0 C226 62 206 252 376 343 L0 343 L0 0 Z" fill="var(--teal)"/>
    </svg>

    <div class="contact">
      <p class="contact-name">MARA ELLISON</p>
      <p class="contact-role">CEO/FOUNDER</p>
      <p class="contact-address">4120 Larkspur Row<br>Halden, Alaska 34810</p>
      <ul class="contact-list">
        <li><svg viewBox="0 0 12 12"><path d="M1 4 Q6 0 11 4 L10 5.5 L8 5 L8 4 Q6 3 4 4 L4 5 L2 5.5 Z M3 6 L9 6 L10 11 L2 11 Z"/></svg>604 555 0182</li>
        <li><svg viewBox="0 0 12 12"><path d="M3 0 H9 V12 H3 Z M4 1.5 V9 H8 V1.5 Z" fill-rule="evenodd"/></svg>604 555 0147</li>
        <li><svg viewBox="0 0 12 12"><path d="M3 1 H9 V4 H3 Z M1 5 H11 V10 H9 V8 H3 V10 H1 Z M3 9 H9 V11 H3 Z"/></svg>604 555 0193</li>
        <li><svg viewBox="0 0 12 12"><path d="M1 3 H11 V10 H1 Z M1.5 3.5 L6 7 L10.5 3.5" stroke="var(--teal)" stroke-width="0.8"/></svg>hello@thebrightwayhaus.ca</li>
        <li><svg viewBox="0 0 12 12"><circle cx="6" cy="6" r="5.5"/><path d="M4 3 Q6 4 5 6 Q7 7 8 9" stroke="var(--teal)" stroke-width="0.9" fill="none"/></svg>www.thebrightwayhaus.ca</li>
      </ul>
    </div>

    <div class="brand brand-front"><span class="brand-mark"></span>BRIGHTWAY HAUS INC.</div>
  </section>

  <section class="card card-back">
    <div class="brand brand-back"><span class="brand-mark"></span>BRIGHTWAY HAUS INC.</div>
    <p class="tagline">Where Shine Counts</p>
  </section>
</body>
</html>
```